Sea Shipping Logistics Company

The business is a logistics company (sea shipping and other special logistics) and also sales of bulk building materials.
The Design should be minimalistic and give a feeling of power and connectivity.
When the client sees the card, they should get a feeling of confident. Dark overall color (background) and print should be red / white .See logo. The card will be printed on trifecta with the middle color being red.

One side should be the logo and a 5 / 6 word slogan
And other side name, contact (phone/email) and a QR Code.

Target Market(s)

Construction companies / Oil & Gas related companies

Industry/Entity Type

Sea Bulk Shipping Logistics

Contact Information for Business Card

Name, Telephone number, Email address, Website URL, QR Code (see description)

Font styles to use
Sans Serif

Requirements
Must have
• No idea
Nice to have
• Minimalistic, but strong and powerful look and feel.

```html
<!DOCTYPE html>
<html lang="en">
<head>
<meta charset="utf-8">
<title>KORVA Business Card</title>
<link href="https://fonts.googleapis.com/css2?family=Roboto:wght@400;500;700;900&display=swap" rel="stylesheet">
<style>
  :root {
    --stage: #878787;
    --ink: #1b1b1d;
    --paper: #ffffff;
    --red: #e93a32;
    --shadow: #1a1a1a;
  }
  * { margin: 0; padding: 0; box-sizing: border-box; }
  html, body { width: 1075px; height: 1200px; overflow: hidden; }
  body {
    background: var(--stage);
    font-family: "Roboto", Arial, sans-serif;
    position: relative;
  }
  .card {
    position: absolute;
    width: 663px;
    height: 395px;
    box-shadow: 3px 3px 0 var(--shadow);
  }
  .card-front { left: 206px; top: 187px; background: var(--paper); }
  .card-back { left: 203px; top: 637px; background: var(--ink); }

  .info-band {
    position: absolute;
    left: 0; top: 75px;
    width: 359px; height: 245px;
    background: var(--ink);
    color: var(--paper);
  }
  .person-name {
    position: absolute; left: 35px; top: 25px;
    font-size: 26px; font-weight: 700; color: var(--red);
    letter-spacing: 0.2px;
  }
  .person-title {
    position: absolute; left: 35px; top: 56px;
    font-size: 19px; font-weight: 400;
  }
  .contact-list {
    position: absolute; left: 35px; top: 146px;
    list-style: none;
    font-size: 19.5px; line-height: 23.5px;
    letter-spacing: 0.3px;
  }
  .contact-list li { display: flex; align-items: center; gap: 6px; }
  .contact-list svg { width: 18px; height: 18px; flex: none; }

  .brand-box {
    position: absolute; left: 370px; top: 75px;
    width: 250px; height: 242px;
    border: 5px solid var(--ink);
    display: flex; align-items: center; justify-content: center;
  }
  .brand-box .brand-name {
    font-size: 62px; font-weight: 900; color: var(--red);
    letter-spacing: -1px;
  }

  .brand-lockup {
    position: absolute; left: 148px; top: 136px;
    display: flex; align-items: flex-start; gap: 8px;
  }
  .brand-square {
    width: 126px; height: 122px;
    border: 3px solid var(--paper);
  }
  .brand-words { color: var(--paper); padding-top: 14px; }
  .brand-words .brand-name {
    display: block;
    font-size: 80px; font-weight: 900; line-height: 66px;
    letter-spacing: -1px;
  }
  .brand-tagline {
    display: block; margin-top: 6px;
    font-size: 18.5px; font-weight: 400; letter-spacing: 0.6px;
  }
</style>
</head>
<body>

<section class="card card-front">
  <div class="info-band">
    <h1 class="person-name">DANIEL REYES</h1>
    <p class="person-title">Managing Director</p>
    <ul class="contact-list">
      <li>
        <svg viewBox="0 0 24 24" aria-hidden="true"><path fill="var(--red)" d="M6.6 10.8a15.1 15.1 0 0 0 6.6 6.6l2.2-2.2c.3-.3.7-.4 1-.2 1.1.4 2.3.6 3.6.6.6 0 1 .4 1 1V20c0 .6-.4 1-1 1A17 17 0 0 1 3 4c0-.6.4-1 1-1h3.5c.6 0 1 .4 1 1 0 1.3.2 2.5.6 3.6.1.3 0 .7-.2 1z"/></svg>
        044-987 654 321
      </li>
      <li>
        <svg viewBox="0 0 24 24" aria-hidden="true"><path fill="var(--red)" d="M2 5h20v14H2z"/><path fill="none" stroke="var(--ink)" stroke-width="1.6" d="M2 5l10 8 10-8M2 19l7-7M22 19l-7-7"/></svg>
        info@korvafreight.com
      </li>
      <li>
        <svg viewBox="0 0 24 24" aria-hidden="true"><g fill="none" stroke="var(--red)" stroke-width="2"><circle cx="12" cy="12" r="9"/><ellipse cx="12" cy="12" rx="4" ry="9"/><path d="M3 12h18M5 7h14M5 17h14"/></g></svg>
        www.korvafreight.com
      </li>
    </ul>
  </div>
  <div class="brand-box">
    <span class="brand-name">KORVA</span>
  </div>
</section>

<section class="card card-back">
  <div class="brand-lockup">
    <div class="brand-square"></div>
    <div class="brand-words">
      <span class="brand-name">KORVA</span>
      <span class="brand-tagline">FREIGHT &amp; LOGISTICS</span>
    </div>
  </div>
</section>

</body>
</html>
```